Social Media App Needs PPT Template

We need a PowerPoint template for a new social media company based in the DC area called "Bold Ledger." We provide an interactive digital platform for executives to share actionable advice. We would like to see designs that use our orange logo color as an accent, but are mainly grey, white, and black. The final design should communicate clean, chic, modern, and professional.

Target Market(s)

Executives

Industry/Entity Type

Information Technology

Font styles to use
Sans Serif

Colors
f78f20
fbe7d2
ffffff
000000
e8e8e8
757575

Requirements
Must have
• My project must have title page and many options for the body of the ppt (graphs, tables, etc). It also needs to be easy to modify. I must have someone who is experienced in creating powerpoint templates.
Nice to have
• It would be nice to have a very modern and clean design that includes the logo on every page, but still leaves a lot of room for the content of the slide
Should not have
• My design project should not look to busy.

```html
<!DOCTYPE html>
<html lang="en">
<head>
<meta charset="utf-8">
<title>Bold Ledger – About Our Company</title>
<link href="https://fonts.googleapis.com/css2?family=Lato:wght@300;400;700&display=swap" rel="stylesheet">
<style>
  :root {
    --orange: #ea8319;
    --orange-light: #f0952a;
    --navy: #232e3d;
    --white: #ffffff;
    --page: #e8e8e8;
    --slide-center: #fbfbfb;
    --slide-edge: #efefef;
    --grey-text: #757575;
    --rule: #8a8a8a;
  }
  html, body {
    margin: 0;
    width: 1200px;
    height: 960px;
    overflow: hidden;
    background: var(--page);
    font-family: "Lato", sans-serif;
  }
  .slide {
    position: absolute;
    left: 0;
    top: 29px;
    width: 1212px;
    height: 910px;
    transform: scale(0.9901);
    transform-origin: 0 0;
    background: radial-gradient(ellipse at 50% 30%, var(--slide-center) 0%, var(--slide-edge) 100%);
    overflow: hidden;
  }
  .slide-shapes { position: absolute; inset: 0; }
  .slide-title {
    position: absolute;
    left: 37px;
    top: 78px;
    margin: 0;
    font-weight: 300;
    font-size: 46px;
    color: var(--white);
    letter-spacing: 0.2px;
  }
  .brand {
    position: absolute;
    right: 42px;
    top: 85px;
    display: flex;
    align-items: center;
    gap: 10px;
    color: var(--white);
    font-weight: 700;
    font-size: 26px;
  }
  .brand-dot {
    width: 22px; height: 22px;
    border-radius: 50%;
    background: var(--orange);
  }
  .data-table {
    position: absolute;
    left: 61px;
    top: 286px;
    width: 1102px;
    border-collapse: collapse;
    border-top: 2px solid var(--rule);
  }
  .data-table th {
    height: 94px;
    font-weight: 700;
    font-size: 18px;
    color: var(--rule);
    text-align: center;
    padding: 0;
  }
  .data-table td {
    height: 95px;
    padding: 0;
    text-align: center;
    font-weight: 300;
    font-size: 36px;
    color: #444;
  }
  .data-table td.row-label {
    width: 370px;
    text-align: left;
    padding-left: 116px;
    box-sizing: border-box;
    font-weight: 400;
    font-size: 24px;
    color: var(--grey-text);
  }
  .data-table th:first-child { width: 370px; }
  .data-table tr.row-dark td { background: var(--navy); color: var(--white); }
  .footer-text {
    position: absolute;
    left: 33px;
    top: 867px;
    font-size: 16px;
    color: #d9dde3;
    font-weight: 400;
  }
</style>
</head>
<body>
  <div class="slide">
    <svg class="slide-shapes" viewBox="0 0 1212 910" width="1212" height="910" aria-hidden="true">
      <defs>
        <linearGradient id="header-orange" x1="0" y1="0" x2="1" y2="0">
          <stop offset="0" stop-color="#e87e17"/>
          <stop offset="0.8" stop-color="#ec8a1f"/>
          <stop offset="1" stop-color="#ef9428"/>
        </linearGradient>
      </defs>
      <!-- top accent strip -->
      <polygon points="945,40 1212,40 1212,52 933,52" fill="var(--orange)"/>
      <!-- header orange band -->
      <polygon points="0,57 920,57 822,153 0,153" fill="url(#header-orange)"/>
      <polygon points="730,57 920,57 858,117 650,117" fill="var(--orange-light)" opacity="0.6"/>
      <!-- header navy logo block -->
      <polygon points="931,57 1212,57 1212,153 833,153" fill="var(--navy)"/>
      <!-- navy strip under header -->
      <polygon points="0,156 818,156 803,169 0,169" fill="var(--navy)"/>
      <!-- footer -->
      <polygon points="0,861 347,861 312,897 0,897" fill="var(--navy)"/>
      <polygon points="353,861 1212,861 1212,897 318,897" fill="var(--orange)"/>
    </svg>

    <h1 class="slide-title">About Our Company</h1>

    <div class="brand"><span class="brand-dot"></span>Bold Ledger</div>

    <table class="data-table">
      <thead>
        <tr><th></th><th>A</th><th>B</th><th>C</th></tr>
      </thead>
      <tbody>
        <tr class="row-dark"><td class="row-label">Type 1</td><td>20</td><td>30</td><td>40</td></tr>
        <tr><td class="row-label">Type 2</td><td>50</td><td>60</td><td>70</td></tr>
        <tr class="row-dark"><td class="row-label">Type 3</td><td>80</td><td>90</td><td>100</td></tr>
      </tbody>
    </table>

    <div class="footer-text">www.boldledger.com &nbsp;|&nbsp; Page 7</div>
  </div>
</body>
</html>
```